Hollow Thicket, a 3d voxel survival video game needs a card for gaming conventions

I am the lead developer for Hollow Thicket http://www.HollowThicket.example and need a business card to hand out at an indie gaming convention
The card would need to include the game name, website url, my name, position (Lead Developer), e-mail and phone number
The game is a 3d, voxel (with smooth terrain) based survival game with guns and wildlife. The main icon of the game would likely be a grizzly bear but I am willing to accept other designs too.
Attached is a media kit for the game with some images you can use but don't have to its just what little art I can provide. Anything on the website or from the video game can also be used. unrelated art can also be used.
Target Market(s)
Indie Developers/publishers at conferences
Industry/Entity Type
Games
Contact Information for Business Card
Name: Corin Waldrick
Position: Lead Developer
E-mail: Pale_Kettle@mailbox.example
Phone number: 555-372-1186

```html
<!DOCTYPE html>
<html lang="en">
<head>
<meta charset="utf-8">
<title>Hollow Thicket – Business Card</title>
<link href="https://fonts.googleapis.com/css2?family=Noto+Sans:wght@400;700&display=swap" rel="stylesheet">
<style>
  :root {
    --page-bg: #d9d4cb;
    --front-light: #c4c0ab;
    --front-mid: #8a8a6c;
    --front-dark: #3d3f27;
    --bear-light: #b08a62;
    --bear-dark: #6e5036;
    --back-light: #2b2b2b;
    --back-dark: #050505;
    --wordmark: #e6dcae;
    --name-red: #d2434b;
    --cream: #e8d9a8;
    --card-shadow: rgba(0, 0, 0, 0.35);
  }
  * { box-sizing: border-box; margin: 0; padding: 0; }
  html, body {
    width: 1200px;
    height: 902px;
    overflow: hidden;
    background: var(--page-bg);
    font-family: "Noto Sans", Verdana, sans-serif;
  }
  .canvas { position: relative; width: 1200px; height: 902px; }

  .card {
    position: absolute;
    width: 600px;
    height: 343px;
    border-radius: 4px;
    overflow: hidden;
    box-shadow: 0 14px 30px var(--card-shadow);
  }

  /* Front side */
  .card-front {
    left: 70px;
    top: 90px;
    background: radial-gradient(ellipse at 42% 40%, var(--front-light) 0%, var(--front-mid) 55%, var(--front-dark) 100%);
  }
  .bear-art {
    position: absolute;
    left: 225px;
    top: 30px;
    width: 230px;
    height: 313px;
    border-radius: 45% 45% 0 0;
    background: radial-gradient(ellipse at 50% 35%, var(--bear-light) 0%, var(--bear-dark) 100%);
    opacity: 0.8;
  }
  .wordmark {
    position: absolute;
    left: 0;
    right: 0;
    text-align: center;
    font-weight: 700;
    color: var(--wordmark);
    letter-spacing: 2px;
    text-transform: uppercase;
    white-space: nowrap;
  }
  .card-front .wordmark { top: 150px; font-size: 44px; }

  /* Back side */
  .card-back {
    left: 540px;
    top: 480px;
    background: linear-gradient(135deg, var(--back-light) 0%, var(--back-dark) 60%);
  }
  .card-back .wordmark { top: 52px; font-size: 38px; }
  .holder {
    position: absolute;
    left: 0;
    right: 0;
    top: 130px;
    text-align: center;
  }
  .holder-name {
    color: var(--name-red);
    font-weight: 700;
    font-size: 22px;
    letter-spacing: 1px;
  }
  .holder-role {
    color: var(--cream);
    font-weight: 700;
    font-size: 15px;
    letter-spacing: 1px;
    margin-top: 2px;
  }
  .contact {
    position: absolute;
    left: 140px;
    right: 20px;
    top: 228px;
    text-align: center;
    color: var(--cream);
    font-size: 15px;
    line-height: 1.55;
    letter-spacing: 0.5px;
    white-space: nowrap;
  }
</style>
</head>
<body>
<main class="canvas">
  <section class="card card-front">
    <div class="bear-art" role="img" aria-label="Photograph of a roaring grizzly bear"></div>
    <h1 class="wordmark">Hollow Thicket</h1>
  </section>

  <section class="card card-back">
    <h2 class="wordmark">Hollow Thicket</h2>
    <div class="holder">
      <p class="holder-name">Corin Waldrick</p>
      <p class="holder-role">Lead Developer</p>
    </div>
    <div class="contact">
      <p class="contact-phone">555-372-1186</p>
      <p class="contact-email">Pale_Kettle@mailbox.example</p>
      <p class="contact-web">www.HollowThicket.example</p>
    </div>
  </section>
</main>
</body>
</html>
```